Modern design company business card design

We are a design oriented construction firm. The owner is an architect and licensed General Contractor and accomplished furniture designer. We do new home construction and large scale remodeling and office design. We would like a design for our new business cards that is clean and modern, but relatable. We like the bright green color of our logo mixed with different shades of grey. We're also open to reinterpreting the logo.

Target Market(s)

Potential design clients,
Construction clients

Industry/Entity Type

Architecture

Contact Information for Business Card

Tall Maple Design | Build Inc. (optional with logo, Inc. optional)Jeffrey MorganOwner (optional)317.555.0148 cell317.431.8056 officejmorgan@greensquareinc.comwww.greensquareinc.com

Font styles to use
Sans Serif
Other font styles liked:
• Avenir

Requirements
Nice to have
• I like designs that have some continuity between the front and back, i.e. similar layouts or graphic elements that wrap around the card. I tend to prefer horizontal over vertical, but that's not a have to. I also tend to prefer white or recycled paper.

```html
<!DOCTYPE html>
<html lang="en">
<head>
<meta charset="utf-8">
<title>Tall Maple Design | Build — Business Cards</title>
<link href="https://fonts.googleapis.com/css2?family=Nunito+Sans:wght@300;400;700&display=swap" rel="stylesheet">
<style>
  :root {
    --backdrop: #e9e7e3;
    --paper: #ffffff;
    --green: #3aa64a;
    --green-dark: #23913a;
    --lime: #a8d14a;
    --lime-light: #c4e077;
    --text-grey: #7d7e81;
    --owner-tint: #d9efc0;
    --white: #ffffff;
  }
  * { box-sizing: border-box; margin: 0; padding: 0; }
  html, body { width: 1200px; height: 913px; overflow: hidden; }
  body {
    background: var(--backdrop);
    font-family: "Nunito Sans", "Avenir", sans-serif;
    position: relative;
  }
  .card {
    position: absolute;
    width: 525px;
    height: 300px;
    border-radius: 16px;
    overflow: hidden;
    box-shadow: 0 10px 28px rgba(0,0,0,.18);
  }
  .card svg.card-art { position: absolute; inset: 0; }
  .card-front { left: 60px; top: 110px; background: var(--paper); }
  .card-back { left: 615px; top: 500px; }

  .company-name {
    position: absolute;
    font-weight: 400;
    font-size: 22px;
    letter-spacing: .3px;
    line-height: 1;
    white-space: nowrap;
  }
  .card-front .company-name { left: 34px; top: 44px; color: var(--text-grey); }
  .card-back .company-name { left: 0; right: 0; top: 72px; text-align: center; color: var(--white); }

  .holder {
    position: absolute;
    right: 26px;
    top: 100px;
    text-align: right;
    color: var(--white);
  }
  .holder-name { font-weight: 700; font-size: 17px; letter-spacing: .5px; text-transform: uppercase; line-height: 1.3; }
  .holder-title { font-weight: 400; font-size: 11px; color: var(--owner-tint); line-height: 1.3; }

  .contact {
    position: absolute;
    left: 26px;
    bottom: 22px;
    list-style: none;
    color: var(--white);
    font-size: 14px;
    font-weight: 300;
  }
  .contact li { display: flex; align-items: center; gap: 10px; height: 22px; }
  .contact-icon { width: 15px; height: 15px; flex: none; }
</style>
</head>
<body>

  <section class="card card-front" aria-label="Business card front">
    <svg class="card-art" width="525" height="300" viewBox="0 0 525 300" aria-hidden="true">
      <defs>
        <linearGradient id="front-grey" x1="0" y1="0" x2="0" y2="1">
          <stop offset="0" stop-color="#6e6f72"/>
          <stop offset="1" stop-color="#4a4b4e"/>
        </linearGradient>
      </defs>
      <rect x="0" y="140" width="525" height="160" fill="url(#front-grey)"/>
      <rect x="0" y="134" width="525" height="8" fill="var(--green)"/>
      <polygon points="290,96 525,96 525,142 345,142 320,156 300,142 290,142" fill="var(--green)"/>
    </svg>

    <div class="company-name">Tall Maple Design | Build</div>

    <div class="holder">
      <div class="holder-name">Dennis Holloway</div>
      <div class="holder-title">Owner</div>
    </div>

    <ul class="contact">
      <li>
        <svg class="contact-icon" viewBox="0 0 16 16" aria-hidden="true"><rect width="16" height="16" rx="2" fill="#fff"/><rect x="5" y="3" width="6" height="10" rx="1" fill="var(--green)"/></svg>
        317.555.0172
      </li>
      <li>
        <svg class="contact-icon" viewBox="0 0 16 16" aria-hidden="true"><rect width="16" height="16" rx="2" fill="#fff"/><path d="M4 4 L6 3.5 L7 6 L6 7 Q7 9 9 10 L10 9 L12.5 10 L12 12 Q7 12.5 4 4 Z" fill="var(--green)"/></svg>
        317.555.0148
      </li>
      <li>
        <svg class="contact-icon" viewBox="0 0 16 16" aria-hidden="true"><rect width="16" height="16" rx="2" fill="#fff"/><circle cx="8" cy="8" r="4.5" fill="none" stroke="var(--green)" stroke-width="1.4"/><line x1="3.5" y1="8" x2="12.5" y2="8" stroke="var(--green)" stroke-width="1.2"/></svg>
        www.tallmapleinc.example
      </li>
      <li>
        <svg class="contact-icon" viewBox="0 0 16 16" aria-hidden="true"><rect width="16" height="16" rx="2" fill="#fff"/><rect x="3" y="4.5" width="10" height="7" fill="none" stroke="var(--green)" stroke-width="1.3"/><polyline points="3,4.5 8,9 13,4.5" fill="none" stroke="var(--green)" stroke-width="1.3"/></svg>
        dholloway@tallmapleinc.example
      </li>
    </ul>
  </section>

  <section class="card card-back" aria-label="Business card back">
    <svg class="card-art" width="525" height="300" viewBox="0 0 525 300" aria-hidden="true">
      <defs>
        <linearGradient id="back-grey" x1="0" y1="0" x2="1" y2="1">
          <stop offset="0" stop-color="#6a6b6e"/>
          <stop offset="1" stop-color="#a3a4a7"/>
        </linearGradient>
        <linearGradient id="back-lime" x1="0" y1="0" x2="1" y2="1">
          <stop offset="0" stop-color="var(--lime)"/>
          <stop offset="1" stop-color="var(--lime-light)"/>
        </linearGradient>
      </defs>
      <rect x="0" y="0" width="525" height="300" fill="url(#back-grey)"/>
      <polygon points="0,190 255,190 275,150 525,150 525,300 0,300" fill="var(--green-dark)"/>
      <polygon points="0,212 268,212 290,166 525,166 525,300 0,300" fill="url(#back-lime)"/>
    </svg>

    <div class="company-name">Tall Maple Design | Build</div>
  </section>

</body>
</html>
```